Copperleaf Roofing Business Card

This is my current business card. But I’d like to make some changes. Somewhere on the card I’d like to list some of the services we offer. Maybe on the back? But I’d still like to keep the red. White and black modern look.

-residential & commercial roofing
-Roof Repairs & Maintenance
-Storm Damage & Insurance Claims specialist
-Christmas Lights and permanent Christmas lights
Fencing. Windows. Gutters. Siding. Sheetrock, painting.

```html
<!DOCTYPE html>
<html lang="en">
<head>
<meta charset="utf-8">
<title>Copperleaf Roofing Business Card</title>
<link rel="stylesheet" href="https://fonts.googleapis.com/css2?family=Orbitron:wght@700;800&family=Poppins:wght@600;700&family=Quicksand:wght@500&display=swap">
<style>
  :root {
    --stage: #dde2e5;
    --card-dark: #1a1a1a;
    --red: #e3222a;
    --red-deep: #8e1a1f;
    --white: #ffffff;
    --text-soft: #f2f2f2;
  }
  * { box-sizing: border-box; margin: 0; padding: 0; }
  html, body { width: 1200px; height: 960px; overflow: hidden; }
  body { background: var(--stage); position: relative; font-family: "Poppins", sans-serif; }

  .card {
    position: absolute;
    left: 250px;
    width: 701px;
    height: 400px;
    background: var(--card-dark);
    overflow: hidden;
  }
  .card--back { top: 60px; }
  .card--front { top: 500px; }

  .brand-name {
    color: var(--white);
    font-family: "Poppins", sans-serif;
    font-weight: 700;
    letter-spacing: 2px;
    white-space: nowrap;
  }
  .brand-name__line { display: block; }

  /* Back */
  .back-mark {
    position: absolute; left: 296px; top: 29px;
    width: 110px; height: 110px; border-radius: 50%;
    background: linear-gradient(135deg, var(--red-deep) 0%, var(--red) 45%, var(--red) 70%, var(--card-dark) 100%);
    border: 2px solid var(--white);
  }
  .back-name {
    position: absolute; left: 0; right: 0; top: 148px;
    text-align: center;
  }
  .back-name .brand-name__line--main { font-size: 29px; line-height: 32px; }
  .back-name .brand-name__line--sub { font-size: 21px; line-height: 26px; letter-spacing: 2.5px; }

  .services {
    position: absolute; left: 0; right: 0; top: 239px;
    text-align: center; list-style: none;
  }
  .services__title {
    color: var(--red); font-family: "Poppins", sans-serif; font-weight: 600;
    font-size: 18px; line-height: 24px; letter-spacing: .5px;
  }
  .services__item {
    color: var(--text-soft); font-family: "Quicksand", sans-serif; font-weight: 500;
    font-size: 16.5px; line-height: 23px; letter-spacing: .6px;
  }

  /* Front */
  .front-panel {
    position: absolute; left: 315px; top: 0; right: 0; bottom: 0;
    background: var(--white);
  }
  .front-artwork {
    position: absolute; left: 311px; top: 11px;
    width: 390px; height: 390px; border-radius: 50%;
    background:
      radial-gradient(circle at 55% 55%, var(--card-dark) 0%, var(--card-dark) 22%, rgba(26,26,26,0) 48%),
      linear-gradient(135deg, var(--red-deep) 0%, var(--red-deep) 35%, var(--red) 55%, var(--red) 100%);
  }
  .front-name {
    position: absolute; left: 24px; top: 20px;
  }
  .front-name .brand-name__line--main { font-size: 33px; line-height: 38px; }
  .front-name .brand-name__line--sub { font-size: 24px; line-height: 30px; letter-spacing: 2.5px; padding-left: 14px; }

  .holder-bar {
    position: absolute; left: 0; top: 171px; width: 15px; height: 56px;
    background: var(--red);
  }
  .holder-name {
    position: absolute; left: 24px; top: 170px;
    font-family: "Orbitron", sans-serif; font-weight: 800; font-size: 28px;
    letter-spacing: 1px; color: var(--white); white-space: nowrap;
  }
  .holder-name__first { color: var(--red); }
  .holder-role {
    position: absolute; left: 25px; top: 206px;
    color: var(--white); font-family: "Poppins", sans-serif; font-weight: 600;
    font-size: 16px; letter-spacing: 1px;
  }
  .contacts { position: absolute; left: 24px; top: 304px; list-style: none; }
  .contact {
    display: flex; align-items: center; gap: 11px; height: 22.5px;
    color: var(--text-soft); font-family: "Quicksand", sans-serif; font-weight: 500;
    font-size: 17px; letter-spacing: .7px;
  }
  .contact svg { width: 16px; height: 16px; flex: none; }
</style>
</head>
<body>
  <section class="card card--back" aria-label="Card back">
    <div class="back-mark" role="img" aria-label="Company emblem artwork"></div>
    <div class="back-name brand-name">
      <span class="brand-name__line brand-name__line--main">COPPERLEAF</span>
      <span class="brand-name__line brand-name__line--sub">ROOFING CO.</span>
    </div>
    <ul class="services">
      <li class="services__title">SERVICES WE OFFER</li>
      <li class="services__item">Roof Repairs &amp; Maintenance</li>
      <li class="services__item">Residential &amp; Commercial Roofing</li>
      <li class="services__item">Storm Damage &amp; Insurance Claims Specialist</li>
      <li class="services__item">Christmas Lights and Permanent Christmas lights</li>
      <li class="services__item">Fencing. Windows. Gutters. Siding. Sheetrock, Painting</li>
    </ul>
  </section>

  <section class="card card--front" aria-label="Card front">
    <div class="front-panel"></div>
    <div class="front-artwork" role="img" aria-label="Large emblem illustration on a red tartan disc"></div>
    <div class="front-name brand-name">
      <span class="brand-name__line brand-name__line--main">COPPERLEAF</span>
      <span class="brand-name__line brand-name__line--sub">ROOFING CO.</span>
    </div>
    <div class="holder-bar"></div>
    <div class="holder-name"><span class="holder-name__first">DANA</span> REYES</div>
    <div class="holder-role">OWNER</div>
    <ul class="contacts">
      <li class="contact">
        <svg viewBox="0 0 24 24" aria-hidden="true"><path fill="var(--red)" d="M6.6 10.8a15 15 0 0 0 6.6 6.6l2.2-2.2c.3-.3.7-.4 1-.2 1.1.4 2.3.6 3.6.6.6 0 1 .4 1 1V20c0 .6-.4 1-1 1A17 17 0 0 1 3 4c0-.6.4-1 1-1h3.5c.6 0 1 .4 1 1 0 1.3.2 2.5.6 3.6.1.3 0 .7-.2 1z"/></svg>
        682-555-0193
      </li>
      <li class="contact">
        <svg viewBox="0 0 24 24" aria-hidden="true"><circle cx="12" cy="12" r="10" fill="var(--red)"/><path d="M2 12h20M12 2c3 3 3 17 0 20M12 2c-3 3-3 17 0 20" stroke="var(--card-dark)" stroke-width="1.3" fill="none"/></svg>
        www.copperleafroofing.co
      </li>
      <li class="contact">
        <svg viewBox="0 0 24 24" aria-hidden="true"><rect x="2" y="6" width="20" height="14" rx="1" fill="var(--red)"/><path d="M2 7l10 7 10-7" stroke="var(--card-dark)" stroke-width="1.5" fill="none"/></svg>
        dana@copperleafroofing.co
      </li>
    </ul>
  </section>
</body>
</html>
```